Business Cards

Need business card design that I can update for new employees and details. Needs to incorporate our logo, be bright and fun (in line with tourism and holidays)
Would like a Map of Western Australia on the front with locations all the caravan parks we own (just purchased Tom Price so please include that as well as others listed on our website).
Target Market(s)
Famillies
Contact Information for Business Card
5 Cards -
Neil Perrow (Director) e: perrow@wattlebay.com.au p: 0491 570 156
Mira Perrow (Director) e: perrow@wattlebay.com.au p: 0491 570 157
Owen Halvey (General Manager) e: halvey@wattlebay.com.au p: 0491 570 158
Helen Halvey (General Manager) e: halvey@wattlebay.com.au p: 0491 570 159
Colin Danby (Training and Operations Manager) - e: danby@wattlebay.com.au p:0491 570 110
Colors
Look and feel

```html
<!DOCTYPE html>
<html lang="en">
<head>
<meta charset="utf-8">
<title>Wattle Bay Tourist Parks – Business Card</title>
<link rel="stylesheet" href="https://fonts.googleapis.com/css2?family=Cinzel:wght@400&family=Roboto:wght@400;500&family=Roboto+Condensed:wght@400;500&display=swap">
<style>
  :root {
    --teal: #00bccb;
    --teal-deep: #06aebd;
    --sea-green: #48b89a;
    --paper: #f6f7f7;
    --ink: #3a3f42;
    --backdrop: #e7eaeb;
    --white: #ffffff;
  }
  * { box-sizing: border-box; margin: 0; padding: 0; }
  html, body {
    width: 1200px;
    height: 800px;
    overflow: hidden;
    background: var(--backdrop);
  }
  .canvas {
    width: 1200px;
    height: 800px;
    display: flex;
    align-items: center;
    justify-content: center;
    gap: 44px;
  }
  .card {
    position: relative;
    width: 540px;
    height: 330px;
    border-radius: 4px;
    overflow: hidden;
    box-shadow: 0 10px 28px rgba(0, 0, 0, 0.14);
  }

  /* Front: personal details */
  .card--front { background: var(--paper); }
  .card__band {
    position: absolute;
    left: 0; top: 0; bottom: 0;
    width: 82px;
    background: var(--teal);
  }
  .brand {
    position: absolute;
    display: flex;
    align-items: center;
    gap: 16px;
    font-family: "Cinzel", serif;
    font-weight: 400;
  }
  .brand__square {
    width: 70px;
    height: 70px;
    flex: none;
  }
  .brand__name {
    line-height: 1.05;
    letter-spacing: 0.12em;
  }
  .brand__name span { display: block; }
  .brand__line-main { font-size: 25px; }
  .brand__line-sub { font-size: 11px; letter-spacing: 0.28em; margin-top: 4px; }

  .card--front .brand { left: 52px; top: 58px; color: var(--ink); }
  .card--front .brand__square {
    background: var(--sea-green);
    border: 4px solid var(--white);
    box-shadow: 0 0 0 2px var(--teal);
  }

  .person {
    position: absolute;
    left: 128px;
    top: 160px;
    font-family: "Roboto Condensed", sans-serif;
  }
  .person__name {
    font-size: 24px;
    font-weight: 500;
    color: var(--teal);
    text-transform: uppercase;
    letter-spacing: 0.01em;
  }
  .person__role {
    font-size: 15px;
    color: var(--sea-green);
    text-transform: uppercase;
    margin-top: 2px;
  }
  .contacts {
    list-style: none;
    margin-top: 18px;
    font-family: "Roboto", sans-serif;
    font-size: 14px;
    color: var(--ink);
  }
  .contacts li {
    display: flex;
    align-items: center;
    gap: 10px;
    margin-bottom: 5px;
  }
  .contacts svg { width: 12px; height: 12px; flex: none; fill: var(--teal); }

  /* Back: brand side */
  .card--back {
    background: var(--teal);
    color: var(--white);
  }
  .card--back .brand {
    left: 50%;
    top: 96px;
    transform: translateX(-50%);
    flex-direction: column;
    gap: 14px;
    color: var(--white);
    text-align: center;
  }
  .card--back .brand__square {
    border: 4px solid var(--white);
    background: var(--sea-green);
  }
  .card--back .brand__line-main { font-size: 30px; }
  .card--back .brand__line-sub { font-size: 13px; }
  .website {
    position: absolute;
    left: 0; right: 0;
    bottom: 44px;
    text-align: center;
    font-family: "Roboto", sans-serif;
    font-size: 14px;
    letter-spacing: 0.16em;
  }
</style>
</head>
<body>
<main class="canvas">

  <section class="card card--front" aria-label="Business card, details side">
    <div class="card__band"></div>
    <div class="brand">
      <div class="brand__square"></div>
      <div class="brand__name">
        <span class="brand__line-main">Wattle Bay</span>
        <span class="brand__line-sub">Tourist Parks</span>
      </div>
    </div>

    <div class="person">
      <p class="person__name">Neil Perrow</p>
      <p class="person__role">Director</p>
      <ul class="contacts">
        <li>
          <svg viewBox="0 0 24 24" aria-hidden="true"><path d="M6.6 10.8a15.1 15.1 0 0 0 6.6 6.6l2.2-2.2a1 1 0 0 1 1-.25 11.4 11.4 0 0 0 3.6.57 1 1 0 0 1 1 1V20a1 1 0 0 1-1 1A17 17 0 0 1 3 4a1 1 0 0 1 1-1h3.5a1 1 0 0 1 1 1c0 1.25.2 2.45.57 3.57a1 1 0 0 1-.25 1z"/></svg>
          0491 570 156
        </li>
        <li>
          <svg viewBox="0 0 24 24" aria-hidden="true"><path d="M2 5h20v14H2z M3 6l9 7 9-7" fill="var(--teal)"/><path d="M3 6.5l9 6.5 9-6.5" fill="none" stroke="#fff" stroke-width="1.6"/></svg>
          perrow@wattlebay.com.au
        </li>
        <li>
          <svg viewBox="0 0 24 24" aria-hidden="true"><circle cx="12" cy="12" r="10"/><path d="M2 12h20M12 2c3 3 3 17 0 20M12 2c-3 3-3 17 0 20" fill="none" stroke="#fff" stroke-width="1.4"/></svg>
          www.wattlebay.com.au
        </li>
      </ul>
    </div>
  </section>

  <section class="card card--back" aria-label="Business card, brand side">
    <div class="brand">
      <div class="brand__square"></div>
      <div class="brand__name">
        <span class="brand__line-main">Wattle Bay</span>
        <span class="brand__line-sub">Tourist Parks</span>
      </div>
    </div>
    <p class="website">www.wattlebay.com.au</p>
  </section>

</main>
</body>
</html>
```